QRTV Membership Web Design Project

We need a website design for QRTV membership. We need something different from what we currently have. See what we currently have: http://www.qorvatu.org/klt4/

Make provision for where members bushiness can be advertised.
Updates

We need a box for advertising members projects/business.

Make provision for where members bushiness / products can be advertised.

Target Market(s)

For members of QRTV and Intending members. Membership is for married men only.

Requirements
Must have
• Make provision for where members bushiness can be advertised.

You are to redesign: http://www.qorvatu.org/klt4/

```html
<!DOCTYPE html>
<html lang="en">
<head>
<meta charset="utf-8">
<title>Men of Renewal — Members Portal</title>
<link rel="stylesheet" href="https://fonts.googleapis.com/css2?family=Ubuntu:wght@300;400;500&display=swap">
<style>
:root{
  --blue:#1f5fa8;
  --blue-dark:#2b5ea6;
  --nav-top:#4d86cc;
  --nav-bottom:#2c63ad;
  --link:#1c5aa0;
  --text:#4b4b4b;
  --muted:#6a6a6a;
  --line:#dcdcdc;
  --band:#f4f4f4;
  --white:#ffffff;
}
*{box-sizing:border-box;margin:0;padding:0}
html,body{width:968px;height:1200px;overflow:hidden;background:var(--white)}
body{font-family:"Ubuntu",sans-serif;color:var(--text);position:relative}
.page{position:relative;width:968px;height:1200px;overflow:hidden}
.abs{position:absolute}

/* header */
.brand{left:30px;top:24px;display:flex;align-items:center;gap:10px}
.brand-mark{width:64px;height:64px;border-radius:50%;background:var(--blue)}
.brand-name{font-size:22px;font-weight:500;color:var(--blue);line-height:1.05}
.brand-name small{display:block;font-size:18px}
.search{left:729px;top:62px;width:200px;height:28px;border:1px solid #cfd8e3;font-size:11px;font-style:italic;color:#6f8bb0;padding:7px 9px}
.search svg{position:absolute;right:8px;top:7px}

/* nav */
.nav{left:0;top:117px;width:968px;height:42px;background:linear-gradient(var(--nav-top),var(--nav-bottom));display:flex}
.nav a{color:var(--white);font-size:13px;text-decoration:none;display:flex;align-items:center;justify-content:center;border-right:1px solid rgba(255,255,255,.35);height:100%}

/* hero */
.hero{left:0;top:159px;width:968px;height:346px;background:linear-gradient(180deg,#fff 0%,#f3f3f3 100%);overflow:hidden}
.hero-title{left:51px;top:56px;font-size:30px;font-weight:500;color:var(--blue)}
.hero-sub{left:50px;top:92px;font-size:23px;font-weight:300;color:#222}
.hero-text{left:48px;top:140px;width:340px;font-size:10.5px;line-height:17px;color:var(--text)}
.hero-text p+p{margin-top:10px}
.btn{display:inline-flex;align-items:center;gap:6px;background:var(--blue-dark);color:var(--white);font-size:12px;border-radius:2px;box-shadow:0 1px 2px rgba(0,0,0,.3)}
.hero-btn{left:50px;top:239px;height:28px;padding:0 12px}
.slider{left:430px;top:18px;width:475px;height:297px;background:var(--white);border:1px solid #ddd;box-shadow:0 1px 4px rgba(0,0,0,.15);padding:5px}
.slide{width:100%;height:100%;background:radial-gradient(ellipse at 50% 60%,#f1c9ad 0%,#e2b79f 35%,#d9dfe8 60%,#c9d4e2 100%)}
.arrow{top:142px;width:28px;height:28px;background:var(--blue-dark);border-radius:2px;display:flex;align-items:center;justify-content:center}

/* features */
.features{left:0;top:505px;width:968px;height:168px;background:var(--band);box-shadow:0 2px 3px rgba(0,0,0,.06)}
.feature{top:0;height:168px;padding-top:28px}
.feature + .feature{border-left:1px dotted #9aaed0}
.feature-icon{position:absolute;top:24px;width:40px;height:58px;border-radius:6px}
.feature h3{font-size:18px;font-weight:400;color:var(--blue)}
.feature p{font-size:10.5px;line-height:17px;color:var(--muted);margin-top:8px;width:210px}
.more{font-size:12px;color:var(--link);margin-top:9px;display:flex;align-items:center;gap:6px}

/* main */
.welcome{left:35px;top:700px;font-size:18px;font-weight:400;color:var(--blue)}
.intro{left:36px;top:736px;width:592px;font-size:10.5px;line-height:18px;color:var(--link)}
.intro p{margin-bottom:18px}
.intro p.tight{margin-bottom:0}
.main-btn{left:32px;top:1036px;height:28px;padding:0 14px}

.side{left:660px;top:698px;width:287px;height:366px;border:1px solid var(--line)}
.side-head{height:45px;background:linear-gradient(var(--nav-top),var(--nav-bottom));color:var(--white);font-size:18px;padding:11px 19px}
.post{padding:12px 18px 0;height:96px;border-bottom:1px solid var(--line)}
.post h4{font-size:13px;font-weight:400;color:var(--blue)}
.post p{font-size:10.5px;line-height:16px;color:var(--muted);margin-top:4px}
.post .more{font-size:10.5px;margin-top:6px}

/* footer */
.footer{left:0;top:1088px;width:968px;height:112px;background:linear-gradient(#f2f2f2,#fafafa)}
.foot-nav{left:29px;top:22px;font-size:11px;color:#333;display:flex;gap:13px}
.foot-nav span.sep{color:#777}
.copy{left:29px;top:52px;font-size:11px;color:#333}
.social{top:19px;width:22px;height:22px;border-radius:3px;background:#666}
</style>
</head>
<body>
<div class="page">

  <header>
    <div class="abs brand">
      <div class="brand-mark"></div>
      <div class="brand-name">Men of Renewal<small>members portal</small></div>
    </div>
    <div class="abs search">Search here..
      <svg width="12" height="12" viewBox="0 0 12 12"><circle cx="5" cy="5" r="3.6" fill="none" stroke="#1f5fa8" stroke-width="1.8"/><line x1="7.6" y1="7.6" x2="11" y2="11" stroke="#1f5fa8" stroke-width="2"/></svg>
    </div>
  </header>

  <nav class="abs nav">
    <a style="width:114px">Home</a>
    <a style="width:114px">About Us</a>
    <a style="width:132px">Membership</a>
    <a style="width:154px">Member Projects</a>
    <a style="width:172px">Membership Levels</a>
    <a style="width:87px">Links</a>
    <a style="width:120px;border-right:none">Contact Us</a>
  </nav>

  <section class="abs hero">
    <svg class="abs" style="left:0;top:0" width="968" height="346" viewBox="0 0 968 346">
      <path d="M0 340 C 150 290, 320 220, 430 110 L430 346 L0 346Z" fill="#ececec"/>
      <path d="M0 340 C 150 290, 320 220, 430 110" fill="none" stroke="#fff" stroke-width="3"/>
    </svg>
    <div class="abs hero-title">Men of Renewal</div>
    <div class="abs hero-sub">tittle line of Jesus Family</div>
    <div class="abs hero-text">
      <p>Brightlane eSolutions is a web service company, offering a wide range of services which range from designing and dev3elopment, that is covering almost all the fields in the best possible way.</p>
      <p>To be the best we know what and how to present beautifully the working of the client’s need and their advantages be highlighted.</p>
    </div>
    <div class="abs btn hero-btn">Learn More
      <svg width="6" height="9" viewBox="0 0 6 9"><path d="M1 1l3.5 3.5L1 8" stroke="#fff" stroke-width="1.5" fill="none"/></svg>
    </div>
    <div class="abs slider">
      <div class="slide" role="img" aria-label="Photo of a smiling baby wrapped in a white towel"></div>
    </div>
    <div class="abs arrow" style="left:432px">
      <svg width="8" height="12" viewBox="0 0 8 12"><path d="M6 1L2 6l4 5" stroke="#fff" stroke-width="1.6" fill="none"/></svg>
    </div>
    <div class="abs arrow" style="left:878px">
      <svg width="8" height="12" viewBox="0 0 8 12"><path d="M2 1l4 5-4 5" stroke="#fff" stroke-width="1.6" fill="none"/></svg>
    </div>
  </section>

  <section class="abs features">
    <div class="abs feature" style="left:0;width:314px;padding-left:82px">
      <div class="feature-icon" style="left:34px;background:linear-gradient(#fbe38a,#e3b21e 70%,#999 71%)" role="img" aria-label="Light bulb illustration"></div>
      <h3>Our Objectives</h3>
      <p>Over years we have built a strong reputation in providing website design and web development services.</p>
      <div class="more">Read more <svg width="6" height="9" viewBox="0 0 6 9"><path d="M1 1l3.5 3.5L1 8" stroke="#1c5aa0" stroke-width="1.5" fill="none"/></svg></div>
    </div>
    <div class="abs feature" style="left:314px;width:319px;padding-left:83px">
      <div class="feature-icon" style="left:22px;background:linear-gradient(#c9a17f 45%,#d39a1f 46%)" role="img" aria-label="Illustration of a member figure"></div>
      <h3>Mebership Level/Benefits</h3>
      <p>Over years we have built a strong reputation in providing website design and web development services.</p>
      <div class="more">Read more <svg width="6" height="9" viewBox="0 0 6 9"><path d="M1 1l3.5 3.5L1 8" stroke="#1c5aa0" stroke-width="1.5" fill="none"/></svg></div>
    </div>
    <div class="abs feature" style="left:633px;width:335px;padding-left:85px">
      <div class="feature-icon" style="left:30px;background:linear-gradient(135deg,#e03a2a 20%,#f5c518 21%,#f2b40d 80%,#555 81%)" role="img" aria-label="Pencil illustration"></div>
      <h3>Registrations</h3>
      <p>Over years we have built a strong reputation in providing website design and web development services.</p>
      <div class="more">Read more <svg width="6" height="9" viewBox="0 0 6 9"><path d="M1 1l3.5 3.5L1 8" stroke="#1c5aa0" stroke-width="1.5" fill="none"/></svg></div>
    </div>
  </section>

  <main>
    <h2 class="abs welcome">Welcome to Our Website Mainpage</h2>
    <div class="abs intro">
      <p>Men of Renewal International Fellowship (QRTV) was established on the 19th day of July 2008 by a group of Christian men from various Church denominations. QRTV is an interdenominational and non-denominational fellowship, born out of a great and overwhelming burden for our generation and a strong desire to see the kingdom of God come and His will be done on Earth as it is in Heaven.</p>
      <p class="tight">Thus, Wanna get ahead in the competition with other websites…. Brightlane esolutions provide you with an attractive and most convincing website to enhance your marketing goals.</p>
      <p>The only way to success is through the right path and that’s what we provide you. None of the other companies has the result we do. So stick to the best that’s how you will be the best don’t opt for the second best. Our expertise does not limit itself to web development but also it includes Web Hosting, Search Engine Optimization, E-Commerce. We partner hundreds of organization to enhance their business, marketing and profit goals.</p>
      <p>Static website is a simple way to get your message out to the public. Static website are cheaper and also it needs less maintenance too. It’s the simplest, cheapest and also the basic thing the search engine picks it up very easily. We at Brightlane provide you the best simple websites too with total work done as using all the best designing and all done so that you can achieve the goal of yours through our work done on your website.</p>
    </div>
    <div class="abs btn main-btn">READ MORE
      <svg width="6" height="9" viewBox="0 0 6 9"><path d="M1 1l3.5 3.5L1 8" stroke="#fff" stroke-width="1.5" fill="none"/></svg>
    </div>

    <aside class="abs side">
      <div class="side-head">Recent Comments &amp; Blog</div>
      <div class="post">
        <h4>20.March.2012</h4>
        <p>Brightlane eSolutions provides you the Search Engine Optimization making your website search engine friendly.</p>
        <div class="more">READ MORE <svg width="6" height="9" viewBox="0 0 6 9"><path d="M1 1l3.5 3.5L1 8" stroke="#1c5aa0" stroke-width="1.5" fill="none"/></svg></div>
      </div>
      <div class="post">
        <h4>20.March.2012</h4>
        <p>E-Commerce is a major progress in technology that has changed the way</p>
        <div class="more">READ MORE <svg width="6" height="9" viewBox="0 0 6 9"><path d="M1 1l3.5 3.5L1 8" stroke="#1c5aa0" stroke-width="1.5" fill="none"/></svg></div>
      </div>
      <div class="post" style="border-bottom:none">
        <h4>20.March.2012</h4>
        <p>E-Commerce is a major progress in technology that has changed the way</p>
        <div class="more">READ MORE <svg width="6" height="9" viewBox="0 0 6 9"><path d="M1 1l3.5 3.5L1 8" stroke="#1c5aa0" stroke-width="1.5" fill="none"/></svg></div>
      </div>
    </aside>
  </main>

  <footer class="abs footer">
    <div class="abs foot-nav">
      <span>Home</span><span class="sep">|</span>
      <span>About Us</span><span class="sep">|</span>
      <span>Membership</span><span class="sep">|</span>
      <span>Member Projects</span><span class="sep">|</span>
      <span>Membership Levels</span><span class="sep">|</span>
      <span>Links</span><span class="sep">|</span>
      <span>Contact Us</span>
    </div>
    <div class="abs copy">Men of Renewal International Fellowship. © 2012. All rights reserved.</div>
    <div class="abs social" style="left:820px" aria-label="Video channel"></div>
    <div class="abs social" style="left:856px" aria-label="Social page"></div>
    <div class="abs social" style="left:896px" aria-label="News feed"></div>
  </footer>

</div>
</body>
</html>
```